Talvex Health Artificial Intelligence MedTech Software Website Refresh

We need a new website (old one at www.talvex-health.example is no longer relevant) for our medtech software company using artificial intelligence to deliver higher quality, faster and more cost effective care in oncology. The audiences are both healthcare providers and health insurance payers. We've created an extensive outline to follow and have the old site still live for easy content use and repurposing. Our primary need is a great overhaul to look and feel. If we find a successful designer, we will need additional work done for graphics and other presentation projects.

Target Market(s)

Health care providers (doctors) and administrators plus health insurers

Industry/Entity Type

Medtech

Coding

Number of Pages Required

5+ page

Font styles to use
Other font styles liked:
• Roboto see Style Guide

Requirements
Must have
• See attached brief
Nice to have
• See attached brief. We like www.caremint.example and www.lumoradx.example as sites.
Should not have
• See attached brief

```html
<!DOCTYPE html>
<html lang="en">
<head>
<meta charset="utf-8">
<title>Talvex Health</title>
<link href="https://fonts.googleapis.com/css2?family=IBM+Plex+Sans:wght@400;500;600;700&display=swap" rel="stylesheet">
<style>
:root{
  --brand:#1f5fae;
  --brand-light:#3a8fd6;
  --icon:#1e7bcf;
  --ink:#1d1d1f;
  --muted:#8a8a8a;
  --soft-bg:#f4f0f1;
  --navy:#2d4a7f;
  --dark:#222222;
  --red:#d9341f;
  --white:#ffffff;
}
*{box-sizing:border-box;margin:0;padding:0}
html,body{width:1200px;height:3264px;overflow:hidden}
body{position:relative;background:var(--white);font-family:"IBM Plex Sans",sans-serif;color:var(--ink)}
.abs{position:absolute}

/* header */
.site-header{left:0;top:0;width:1200px;height:87px;background:var(--white)}
.brand{left:133px;top:24px;display:flex;align-items:center;gap:8px;color:var(--brand);font-weight:700;font-size:26px}
.brand-dot{width:12px;height:12px;border-radius:50%;background:var(--brand-light)}
.nav a{position:absolute;top:38px;font-size:15px;font-weight:500;color:var(--ink);text-decoration:none;letter-spacing:.2px}

/* hero */
.hero-art{left:0;top:87px;width:1200px;height:546px;
  background:
    radial-gradient(ellipse 300px 260px at 960px 330px, rgba(120,150,210,.55), rgba(120,150,210,0) 70%),
    radial-gradient(ellipse 260px 220px at 700px 330px, rgba(250,245,240,.55), rgba(250,245,240,0) 70%),
    radial-gradient(ellipse 230px 120px at 520px 240px, rgba(150,190,230,.5), rgba(150,190,230,0) 70%),
    radial-gradient(ellipse 120px 110px at 80px 310px, rgba(240,180,40,.55), rgba(240,180,40,0) 70%),
    linear-gradient(180deg,#e4cdbb 0%,#dcc3b1 72%,#c9cfe0 86%,#b8c9e6 100%)}
.hero-panel{left:130px;top:274px;width:300px;height:194px;background:rgba(60,55,52,.84)}
.hero-title{left:156px;top:292px;color:var(--white);font-weight:700;font-size:37px;line-height:37px;text-transform:uppercase}
.btn-read{left:157px;top:417px;width:109px;height:30px;background:var(--brand);color:var(--white);font-size:12px;font-weight:600;display:flex;align-items:center;justify-content:center}
.dots{left:551px;top:584px;display:flex;gap:13px}
.dots span{width:9px;height:9px;border-radius:50%;background:rgba(255,255,255,.8)}
.dots .on{background:var(--red)}

/* section titles */
.section-title{left:0;width:1200px;text-align:center;font-weight:700;font-size:25px;letter-spacing:.3px}
.rule{left:576px;width:48px;height:2px;background:#9a9a9a}

/* services */
.service-icon{width:84px;height:84px}
.service{width:300px;text-align:center}
.service h3{font-size:14px;font-weight:700}
.service p{font-size:13px;margin-top:10px}

/* leadership */
.leadership{left:0;top:979px;width:1200px;height:521px;background:var(--soft-bg)}
.card{top:1092px;width:289px;height:361px;background:var(--white);border:1px solid #e4e0e0}
.card .photo{height:179px;background:radial-gradient(ellipse 90px 110px at 50% 60%,#c99a80,#a5b7cf 75%),#a5b7cf}
.card h4{margin-top:27px;font-size:14px;font-weight:600;text-align:center;text-transform:uppercase}
.card .role{margin-top:6px;font-size:13px;color:var(--muted);text-align:center}
.card .bio{margin:18px auto 0;width:232px;font-size:11.5px;line-height:17.5px;text-align:center}
.chev{width:16px;height:28px}

/* feature rows */
.feature h2{font-size:25px;font-weight:700;letter-spacing:.3px}
.feature p{margin-top:22px;font-size:17.5px;line-height:24px;width:300px}
.illus-providers{left:136px;top:1571px;width:490px;height:317px;
  background:
    radial-gradient(ellipse 110px 150px at 340px 70px, rgba(40,150,230,.7), rgba(40,150,230,0) 70%),
    radial-gradient(ellipse 150px 150px at 240px 170px, rgba(60,110,220,.45), rgba(60,110,220,0) 70%),
    radial-gradient(ellipse 120px 60px at 440px 170px, rgba(245,180,60,.45), rgba(245,180,60,0) 70%),
    radial-gradient(ellipse 120px 80px at 100px 260px, rgba(40,140,150,.35), rgba(40,140,150,0) 70%),
    #ffffff}
.illus-payers{left:576px;top:1932px;width:444px;height:376px;
  background:
    radial-gradient(ellipse 90px 130px at 110px 280px, rgba(220,50,50,.45), rgba(220,50,50,0) 70%),
    radial-gradient(ellipse 140px 180px at 220px 200px, rgba(40,70,130,.4), rgba(40,70,130,0) 70%),
    radial-gradient(ellipse 220px 190px at 260px 210px, rgba(170,200,235,.8), rgba(170,200,235,0) 75%),
    #ffffff}

/* evidence */
.evidence{left:0;top:2370px;width:1200px;height:412px;background:var(--navy)}
.quote-col{width:270px;text-align:center;color:var(--white)}
.quote-col .mark{font-size:56px;font-weight:700;line-height:44px;height:34px;font-family:Georgia,serif}
.quote-col h5{margin-top:22px;font-size:12px;font-weight:700;line-height:16px;letter-spacing:.4px;text-transform:uppercase}
.quote-col p{margin-top:18px;font-size:13.5px;line-height:19px}

/* contact */
.contact{left:0;top:2782px;width:1200px;height:420px;background:var(--dark)}
.contact-info{left:133px;top:2895px;width:400px;color:var(--white)}
.contact-info .label{font-size:12px;font-weight:700;letter-spacing:.3px}
.contact-info .value{font-size:14.5px;line-height:19px;margin-top:6px;color:#e8e8e8}
.field{left:688px;width:380px;border:1px solid #cfcfcf;color:#e6e6e6;font-size:12.5px;padding:0 16px;display:flex;align-items:center}
.field.msg{align-items:flex-start;padding-top:14px}
.btn-quote{left:689px;top:3110px;width:192px;height:41px;background:var(--red);color:var(--white);font-weight:700;font-size:17px;display:flex;align-items:center;justify-content:center}

/* footer */
.footer-text{top:3226px;font-size:11.5px;color:var(--ink)}
.social{top:3220px;width:26px;height:26px;border-radius:50%}
</style>
</head>
<body>

<header class="abs site-header">
  <div class="abs brand"><span class="brand-dot"></span>Talvex Health</div>
  <nav class="nav">
    <a style="left:545px">HOME</a>
    <a style="left:630px">TECHNOLOGY</a>
    <a style="left:771px">COMPANY</a>
    <a style="left:886px">EVIDENCE</a>
    <a style="left:1002px">CONTACT</a>
  </nav>
</header>

<div class="abs hero-art" role="img" aria-label="Illustration of a humanoid robot taking the pulse of an elderly patient in a living room, with floating heart-rate data screens"></div>
<div class="abs hero-panel"></div>
<h1 class="abs hero-title">Artificial<br>Intelligence<br>Health Care</h1>
<div class="abs btn-read">READ MORE</div>
<div class="abs dots"><span></span><span></span><span class="on"></span><span></span><span></span></div>

<h2 class="abs section-title" style="top:682px">OUR SERVICES</h2>
<div class="abs rule" style="top:726px"></div>

<svg class="abs service-icon" style="left:225px;top:771px" viewBox="0 0 84 84" role="img" aria-label="Patient icon">
  <circle cx="42" cy="14" r="8" fill="var(--icon)"/>
  <path d="M18 30 H66 V38 H52 V70 H46 V52 H38 V70 H32 V38 H18 Z" fill="var(--icon)"/>
  <path d="M14 42 A30 30 0 0 0 30 74" fill="none" stroke="var(--icon)" stroke-width="4"/>
  <path d="M70 42 A30 30 0 0 1 54 74" fill="none" stroke="var(--icon)" stroke-width="4"/>
</svg>
<svg class="abs service-icon" style="left:557px;top:771px" viewBox="0 0 84 84" role="img" aria-label="Payer icon, hand holding a coin">
  <circle cx="55" cy="24" r="15" fill="var(--icon)"/>
  <text x="55" y="30" text-anchor="middle" font-family="IBM Plex Sans,sans-serif" font-size="18" font-weight="700" fill="#fff">$</text>
  <path d="M4 56 L18 48 Q30 44 40 50 L52 52 Q58 54 54 58 L38 58 L56 60 L74 48 Q80 46 78 52 L62 68 Q56 72 46 72 L22 72 L12 78 Z" fill="var(--icon)"/>
</svg>
<svg class="abs service-icon" style="left:936px;top:771px" viewBox="0 0 84 84" role="img" aria-label="Provider icon, person with arrows and coin">
  <circle cx="42" cy="38" r="10" fill="var(--icon)"/>
  <path d="M24 76 Q24 54 42 54 Q60 54 60 76 Z" fill="var(--icon)"/>
  <g stroke="var(--icon)" stroke-width="3" fill="none" stroke-linecap="round">
    <path d="M42 20 V6 M37 11 L42 6 L47 11"/>
    <path d="M24 26 L14 16 M14 23 V16 H21"/>
    <path d="M60 26 L70 16 M63 16 H70 V23"/>
    <path d="M20 42 H6 M11 37 L6 42 L11 47"/>
    <path d="M64 42 H78 M73 37 L78 42 L73 47"/>
  </g>
  <circle cx="66" cy="68" r="10" fill="#fff" stroke="var(--icon)" stroke-width="3"/>
  <text x="66" y="73" text-anchor="middle" font-family="IBM Plex Sans,sans-serif" font-size="13" font-weight="700" fill="var(--icon)">$</text>
</svg>

<div class="abs service" style="left:116px;top:873px"><h3>PATIENT</h3><p>30% Reduction in side effects</p></div>
<div class="abs service" style="left:447px;top:873px"><h3>PAYER</h3><p>$15M PMPY</p></div>
<div class="abs service" style="left:827px;top:873px"><h3>PROVIDER</h3><p>$4k/Patient</p></div>

<section class="abs leadership"></section>
<h2 class="abs section-title" style="top:1021px">LEADER SHIP</h2>

<svg class="abs chev" style="left:82px;top:1259px" viewBox="0 0 16 28"><path d="M14 2 L3 14 L14 26" fill="none" stroke="#9a9a9a" stroke-width="2"/></svg>
<svg class="abs chev" style="left:1104px;top:1259px" viewBox="0 0 16 28"><path d="M2 2 L13 14 L2 26" fill="none" stroke="#9a9a9a" stroke-width="2"/></svg>

<article class="abs card" style="left:143px">
  <div class="photo" role="img" aria-label="Portrait photo of the president"></div>
  <h4>Rowan Ellery, PhD</h4>
  <div class="role">President and Chief Executive Officer</div>
  <p class="bio">Leadership in radiology and therapeutic radiology technology creation. Experience introducing products to the radiation oncology market.</p>
</article>
<article class="abs card" style="left:460px">
  <div class="photo" role="img" aria-label="Portrait photo of the vice president of sales"></div>
  <h4>Marisol Tan</h4>
  <div class="role">Vice President of Sales</div>
  <p class="bio">Executive sales leadership and business development across software, media and healthcare (Vision, Brightwave Media, Corvane).</p>
</article>
<article class="abs card" style="left:780px">
  <div class="photo" role="img" aria-label="Portrait photo of the director of engineering"></div>
  <h4>Derek L. Holloway, PhD</h4>
  <div class="role">Director of Engineering</div>
  <p class="bio">Expertise in computer vision, data mining of medical databases and Artificial Intelligence. Hartfield PhD and data mining fellowship at the Northbridge Health Institute.</p>
</article>

<div class="abs illus-providers" role="img" aria-label="Illustration of doctors walking beside a large medical tablet with charts"></div>
<div class="abs feature" style="left:682px;top:1666px">
  <h2>FOR PROVIDERS</h2>
  <p>Creating a treatment directive starts from scratch for every patient and is a time consuming iterative/back and forth process</p>
</div>

<div class="abs feature" style="left:179px;top:2030px">
  <h2>FOR PAYERS</h2>
  <p style="width:325px">there is no transparency to the uniqueness of the patient so the process has costly delays to gather more information and align the treatment to what's best for the patient; often attempts to redirect care are unfruitful</p>
</div>
<div class="abs illus-payers" role="img" aria-label="Illustration of a mother and child with a doctor beside a large checklist clipboard and medical items"></div>

<section class="abs evidence"></section>
<h2 class="abs section-title" style="top:2420px;color:var(--white)">CLINICAL EVIDENCE</h2>
<div class="abs rule" style="top:2464px;background:var(--white)"></div>

<svg class="abs chev" style="left:62px;top:2592px" viewBox="0 0 16 28"><path d="M14 2 L3 14 L14 26" fill="none" stroke="#ffffff" stroke-width="2.5"/></svg>
<svg class="abs chev" style="left:1124px;top:2592px" viewBox="0 0 16 28"><path d="M2 2 L13 14 L2 26" fill="none" stroke="#ffffff" stroke-width="2.5"/></svg>

<div class="abs quote-col" style="left:123px;top:2528px">
  <div class="mark">&ldquo;</div>
  <h5>L. R. Fenwick, K.<br>M. Ostrander, P. Vale</h5>
  <p>Quantifying temporal trends and the impact of advances in radiation planning on heart and lung dose for lung cancer treatment using a machine learning model</p>
</div>
<div class="abs quote-col" style="left:464px;top:2528px">
  <div class="mark">&ldquo;</div>
  <h5>Nora Lindqvist, Theo K. Baird,<br>and Elias J. Morrow</h5>
  <p>Leveraging Artificial Intelligence (AI) clinical decision support software to improve treatment plan quality in head and neck cancer patients</p>
</div>
<div class="abs quote-col" style="left:819px;top:2528px">
  <div class="mark">&ldquo;</div>
  <h5>Ivo Castell, Mei S. Arden,<br>Jonah Pryce</h5>
  <p>Implementation and impact of AI decision support software on treatment planning workflow</p>
</div>

<section class="abs contact"></section>
<h2 class="abs" style="left:132px;top:2805px;color:var(--white);font-size:25px;font-weight:700">CONTACT US</h2>
<div class="abs contact-info">
  <div class="label">ADDRESS</div>
  <div class="value">480 Harborview Road<br>Suite 310, Fairmont, CA 94000</div>
  <div class="label" style="margin-top:22px">PHONE</div>
  <div class="value">(555) 012-4179</div>
  <div class="label" style="margin-top:22px">E MAIL</div>
  <div class="value">support@talvex-health.example</div>
</div>

<div class="abs field" style="top:2836px;height:42px">Name</div>
<div class="abs field" style="top:2891px;height:43px">E mail</div>
<div class="abs field" style="top:2947px;height:42px">Phone</div>
<div class="abs field msg" style="top:2998px;height:95px">Message</div>
<div class="abs btn-quote">REQUEST A QUOTE</div>

<div class="abs footer-text" style="left:133px">Disclaimer &nbsp;&nbsp; | &nbsp;&nbsp;Copyright © 2020 All Rights Reserved</div>
<div class="abs footer-text" style="left:908px">Follow us</div>
<div class="abs social" style="left:972px;background:#2b5aa8"></div>
<div class="abs social" style="left:1006px;background:#2e8fe0"></div>
<div class="abs social" style="left:1040px;background:#1d2a5a"></div>

</body>
</html>
```